Acupuncture business needs business card design

I need a business card for an acupuncture clinic called "Harbourlight Wellness"
It will need the following details:
My name: Marcus Pelling
Acupuncturist
Member TVBH
KWF Treatment Provider
Ph numbers: 581 2734 027 418 5620
Email: marcus@hbwel.example.nz
On the back it will need a table with 2 columns for appointments, one column for time and one for date.

Industry/Entity Type

Clinic

Contact Information for Business Card

Marcus Pelling
Acupuncturist
Member TVBH
KWF Treatment Provider
Email: marcus@hbwel.example.nz

Requirements
Must have
• Marcus Pelling
• Acupuncturist
• Member TVBH
• KWF Treatment Provider
• Ph numbers: 581 2734 027 418 5620
• Email: marcus@hbwel.example.nz
• On the back it will need a table with 2 columns for appointments, one column for time and one for date.

```html
<!DOCTYPE html>
<html lang="en">
<head>
<meta charset="utf-8">
<title>Harbourlight Wellness – Business Card</title>
<link rel="stylesheet" href="https://fonts.googleapis.com/css2?family=Ubuntu:wght@400;500;700&family=Open+Sans:wght@400;600&display=swap">
<style>
  :root {
    --bg: #2e2e2e;
    --card: #ffffff;
    --cyan: #17a3dc;
    --teal: #0f6d88;
    --teal-deep: #0b5a73;
    --ink: #1f1f1f;
    --rule: #9a9a9a;
  }
  * { box-sizing: border-box; margin: 0; padding: 0; }
  html, body {
    width: 1200px; height: 1000px; overflow: hidden;
    background: var(--bg);
    font-family: "Open Sans", Arial, sans-serif;
    color: var(--ink);
  }
  .sheet {
    position: relative; width: 1200px; height: 1000px;
    display: flex; flex-direction: column; align-items: center;
    justify-content: center; gap: 40px;
  }
  .card {
    position: relative; width: 722px; height: 440px;
    background: var(--card); overflow: hidden;
    box-shadow: 0 14px 30px rgba(0,0,0,.45);
  }
  .brand {
    position: absolute; display: flex; align-items: center; gap: 18px;
  }
  .brand-dot {
    width: 58px; height: 58px; border-radius: 50%; background: var(--teal);
  }
  .brand-name {
    font-family: "Ubuntu", sans-serif; font-weight: 500;
    font-size: 46px; color: var(--cyan); letter-spacing: -0.5px;
  }
  /* front */
  .card-front .brand { top: 62px; left: 60px; }
  .wave { position: absolute; left: 0; bottom: 0; width: 722px; height: 440px; }
  .person { position: absolute; top: 178px; left: 60px; }
  .person-name {
    font-family: "Ubuntu", sans-serif; font-weight: 500;
    font-size: 30px; color: var(--cyan); margin-bottom: 6px;
  }
  .person-role { font-size: 19px; line-height: 1.3; }
  .divider {
    position: absolute; top: 180px; left: 386px; width: 1px; height: 118px;
    background: var(--rule);
  }
  .contacts { position: absolute; top: 186px; left: 412px; list-style: none; }
  .contacts li {
    display: flex; align-items: center; gap: 14px;
    font-size: 20px; height: 38px;
  }
  .icon { width: 22px; height: 22px; flex: none; }
  /* back */
  .card-back .brand { top: 46px; left: 60px; }
  .appt-title {
    position: absolute; top: 128px; left: 138px;
    font-family: "Ubuntu", sans-serif; font-weight: 500;
    font-size: 30px; color: var(--teal);
  }
  .appt-table {
    position: absolute; top: 200px; left: 60px; width: 602px;
    border-collapse: collapse;
  }
  .appt-table td { height: 56px; vertical-align: bottom; padding-bottom: 6px; font-size: 20px; }
  .appt-label { width: 96px; white-space: nowrap; }
  .appt-line { border-bottom: 1px solid var(--rule); }
  .appt-line.date { width: 300px; }
  .appt-label.time { width: 70px; padding-left: 24px; }
</style>
</head>
<body>
<main class="sheet">

  <section class="card card-front" aria-label="Front of card">
    <svg class="wave" viewBox="0 0 722 440" aria-hidden="true">
      <defs>
        <linearGradient id="bandShade" x1="0" y1="0" x2="1" y2="0">
          <stop offset="0" stop-color="#0f6d88"/>
          <stop offset="0.7" stop-color="#137891"/>
          <stop offset="1" stop-color="#0b5a73"/>
        </linearGradient>
      </defs>
      <path d="M0 318 Q300 330 722 418 L722 440 L0 440 Z" fill="url(#bandShade)"/>
      <path d="M0 318 Q300 330 722 418" fill="none" stroke="#17a3dc" stroke-width="5"/>
    </svg>

    <div class="brand">
      <span class="brand-dot"></span>
      <span class="brand-name">Harbourlight Wellness</span>
    </div>

    <div class="person">
      <p class="person-name">Marcus Pelling</p>
      <p class="person-role">Acupuncturist</p>
      <p class="person-role">Member TVBH</p>
      <p class="person-role">KWF Treatment Provider</p>
    </div>

    <div class="divider"></div>

    <ul class="contacts">
      <li>
        <svg class="icon" viewBox="0 0 22 22" aria-hidden="true"><rect width="22" height="22" rx="4" fill="#17a3dc"/><path d="M7 5c1 0 1.5 2.5 1.5 3S7.5 9 7.5 9.5c.5 1.5 2 3 3.5 3.5.5 0 1-1 1.5-1s3 .5 3 1.5-1 2.5-2.5 2.5C9 16 6 13 6 8.5 6 6 6.5 5 7 5z" fill="#fff"/></svg>
        <span>581 2734</span>
      </li>
      <li>
        <svg class="icon" viewBox="0 0 22 22" aria-hidden="true"><rect width="22" height="22" rx="4" fill="#17a3dc"/><path d="M7 5c1 0 1.5 2.5 1.5 3S7.5 9 7.5 9.5c.5 1.5 2 3 3.5 3.5.5 0 1-1 1.5-1s3 .5 3 1.5-1 2.5-2.5 2.5C9 16 6 13 6 8.5 6 6 6.5 5 7 5z" fill="#fff"/></svg>
        <span>027 418 5620</span>
      </li>
      <li>
        <svg class="icon" viewBox="0 0 22 22" aria-hidden="true"><rect width="22" height="22" rx="4" fill="#17a3dc"/><rect x="5" y="7" width="12" height="8" fill="none" stroke="#fff" stroke-width="1.5"/><path d="M5 7l6 5 6-5" fill="none" stroke="#fff" stroke-width="1.5"/></svg>
        <span>marcus@hbwel.example.nz</span>
      </li>
    </ul>
  </section>

  <section class="card card-back" aria-label="Back of card">
    <div class="brand">
      <span class="brand-dot"></span>
      <span class="brand-name">Harbourlight Wellness</span>
    </div>

    <h2 class="appt-title">Your Next Appointment</h2>

    <table class="appt-table">
      <tr><td class="appt-label">Day/Date</td><td class="appt-line date"></td><td class="appt-label time">Time</td><td class="appt-line"></td></tr>
      <tr><td class="appt-label">Day/Date</td><td class="appt-line date"></td><td class="appt-label time">Time</td><td class="appt-line"></td></tr>
      <tr><td class="appt-label">Day/Date</td><td class="appt-line date"></td><td class="appt-label time">Time</td><td class="appt-line"></td></tr>
      <tr><td class="appt-label">Day/Date</td><td class="appt-line date"></td><td class="appt-label time">Time</td><td class="appt-line"></td></tr>
    </table>
  </section>

</main>
</body>
</html>
```